Certificate of Completion and Appreciation

We are a training center that needs a design for a certificate of Completion, Attendance, and Appreciation.

We change our name from LOOM Venture Academy to LOOM Venture Center. So please to make the change in the Logo.

The following is the text we need in the certificate:

LOOM Venture Center

Certifies that

____________ (Link where the name of the student will be typed)

has successfully completed

______________ (Line where the name of the course)

_______________
Tariq Bin Sadoun
C.E.O

_______________
Another Name
Lead Trainer

_______________
Another Name
Course Director

Please let me know if you have any questions.

Target Market(s)

Young and trendy men and women age 25 to 40

Industry/Entity Type

Training

Font styles to use
Sans Serif

Requirements
Must have
• Size of the certificate should be A4
Nice to have
• White background (not necesserly plain)
Should not have
• Too many colors. You must stick to the colors of the logo.

```html
<!DOCTYPE html>
<html lang="en">
<head>
<meta charset="utf-8">
<title>LOOM Venture Center – Certificate of Completion</title>
<link rel="stylesheet" href="https://fonts.googleapis.com/css2?family=Lato:wght@400;700;900&display=swap">
<style>
  :root {
    --paper: #fbfbfa;
    --ink: #2a2a2a;
    --ink-soft: #6d6d6d;
    --brand-blue: #17679e;
    --frame-line: #7a7a7a;
    --rule: #b9b9b9;
  }
  * { box-sizing: border-box; margin: 0; padding: 0; }
  html, body {
    width: 1200px;
    height: 874px;
    overflow: hidden;
    background: var(--paper);
    font-family: "Lato", sans-serif;
    color: var(--ink);
  }
  .certificate {
    position: relative;
    width: 1200px;
    height: 874px;
    background: var(--paper);
  }
  .border-frame {
    position: absolute;
    left: 0; top: 0;
  }
  .brand {
    position: absolute;
    top: 178px;
    left: 0;
    width: 100%;
    display: flex;
    justify-content: center;
    align-items: center;
    gap: 16px;
  }
  .brand-dot {
    width: 44px;
    height: 44px;
    border-radius: 50%;
    background: var(--brand-blue);
  }
  .brand-name {
    font-weight: 900;
    font-size: 46px;
    letter-spacing: 1px;
    color: var(--ink);
    line-height: 1;
  }
  .centered {
    position: absolute;
    left: 0;
    width: 100%;
    text-align: center;
  }
  .title {
    top: 282px;
    font-size: 56px;
    font-weight: 900;
    color: var(--brand-blue);
    letter-spacing: 0.5px;
  }
  .certify-line {
    top: 380px;
    font-size: 24px;
    font-weight: 700;
    letter-spacing: 0.5px;
  }
  .name-rule {
    position: absolute;
    left: 440px;
    width: 320px;
    height: 1px;
    background: var(--rule);
  }
  .name-rule.upper { top: 430px; }
  .name-rule.lower { top: 497px; }
  .recipient {
    top: 438px;
    font-size: 42px;
    font-weight: 400;
  }
  .completed-line {
    top: 521px;
    font-size: 20px;
    color: var(--ink-soft);
  }
  .course {
    top: 556px;
    font-size: 33px;
    font-weight: 400;
  }
  .date-line {
    top: 608px;
    font-size: 17px;
    color: var(--ink-soft);
  }
  .signatories {
    position: absolute;
    top: 686px;
    left: 191px;
    width: 820px;
    display: flex;
    justify-content: space-between;
  }
  .signatory {
    width: 220px;
    text-align: center;
    border-top: 1px solid var(--frame-line);
    padding-top: 8px;
    font-size: 15px;
    line-height: 1.3;
    color: var(--ink-soft);
  }
</style>
</head>
<body>
<main class="certificate">
  <svg class="border-frame" width="1200" height="874" viewBox="0 0 1200 874" aria-hidden="true">
    <rect x="49" y="71" width="1102" height="730" fill="none" stroke="var(--frame-line)" stroke-width="3"/>
    <rect x="60" y="82" width="1080" height="708" fill="none" stroke="var(--frame-line)" stroke-width="1.5"/>
    <g fill="none" stroke="var(--frame-line)" stroke-width="1.5">
      <rect x="43" y="65" width="14" height="14"/>
      <rect x="1143" y="65" width="14" height="14"/>
      <rect x="43" y="793" width="14" height="14"/>
      <rect x="1143" y="793" width="14" height="14"/>
    </g>
  </svg>

  <header class="brand">
    <span class="brand-dot"></span>
    <span class="brand-name">LOOM Venture Center</span>
  </header>

  <h1 class="centered title">CERTIFICATE OF COMPLETION</h1>
  <p class="centered certify-line">THIS IS TO CERTIFY THAT</p>

  <span class="name-rule upper"></span>
  <p class="centered recipient">Arjun Mehra</p>
  <span class="name-rule lower"></span>

  <p class="centered completed-line">has successfully completed the</p>
  <p class="centered course">Post Graduate Programme in Management</p>
  <p class="centered date-line">on this 28th day of February, 2015</p>

  <footer class="signatories">
    <div class="signatory">Tariq Bin Sadoun<br>C.E.O</div>
    <div class="signatory">Another Name<br>Lead Trainer</div>
    <div class="signatory">Janother Name<br>Course Director</div>
  </footer>
</main>
</body>
</html>
```